Local Flower Farm Needs Business Card Design

I need business cards designed for a flower farm based in Eudora, Kansas.
Business Info:
We are a local cut flower farm located in Eudora, Kansas, founded by Corinne Haldwick. What started as a passion for agriculture and search for more joy in daily life has blossomed into a small business dedicated to providing the community with beautiful, fresh, and sustainable flowers. We specialize in local, seasonal blooms, ensuring that every petal reflects the care and dedication we pour into our craft. Our mission is to deliver the highest quality flowers directly to our customers through local farmers markets and to florists who share our commitment to sustainability. Join us in celebrating the beauty of nature, one bloom at a time!
Contact Details:
Corinne Haldwick
Owner
Phone 913-555-0147
Facebook: Rosalind Thorpe Gardens
Instagram: @RosalindThorpeGardens
Website: RosalindThorpeGardens.example
Target Market(s)
Wholesale to Florists and Direct to Consumer via Farmers Market
Industry/Entity Type
Florist, Farm
Contact Information for Business Card
Name, Contact Info, Logo
Look and feel
Each slider illustrates characteristics of the customer's brand and the style your logo design should communicate.

```html
<!DOCTYPE html>
<html lang="en">
<head>
<meta charset="utf-8">
<title>Rosalind Thorpe Gardens – Business Card</title>
<link href="https://fonts.googleapis.com/css2?family=Libre+Baskerville:wght@400;700&display=swap" rel="stylesheet">
<style>
  :root {
    --backdrop: #2b2b2b;
    --card: #0c2a2e;
    --ink: #ffffff;
    --rule: rgba(255,255,255,0.85);
  }
  * { margin: 0; padding: 0; box-sizing: border-box; }
  html, body { width: 1200px; height: 689px; overflow: hidden; background: var(--backdrop); }
  body { font-family: "Libre Baskerville", Georgia, serif; color: var(--ink); position: relative; }

  .card {
    position: absolute;
    top: 190px;
    width: 540px;
    height: 309px;
    background: var(--card);
    border-radius: 22px;
    box-shadow: 0 18px 40px rgba(0,0,0,0.45);
    overflow: hidden;
  }
  .card--front { left: 30px; }
  .card--back { left: 630px; }

  .brand-mark {
    position: absolute;
    display: flex;
    align-items: center;
    justify-content: center;
    text-align: center;
    border: 1px solid var(--rule);
    border-radius: 50%;
    font-weight: 400;
    text-transform: uppercase;
    letter-spacing: 0.14em;
    line-height: 1.5;
  }
  .card--front .brand-mark {
    width: 210px; height: 210px;
    left: 165px; top: 50px;
    font-size: 17px;
  }
  .card--back .brand-mark {
    width: 140px; height: 140px;
    right: 40px; top: 20px;
    font-size: 11px;
  }

  .contact-block {
    position: absolute;
    left: 34px;
    right: 28px;
    top: 118px;
  }
  .contact-block .name {
    font-size: 26px;
    font-weight: 700;
    line-height: 1.2;
    letter-spacing: 0.01em;
  }
  .contact-block .role {
    font-size: 12px;
    line-height: 1.3;
    margin-top: 4px;
  }
  .contact-block .divider {
    width: 100%;
    height: 1px;
    background: var(--rule);
    margin: 10px 0 10px;
  }
  .contact-list { list-style: none; font-size: 13px; line-height: 1.6; }
  .contact-list li { display: flex; align-items: center; gap: 8px; }
  .contact-list .dot {
    width: 10px; height: 10px; border-radius: 50%;
    background: var(--ink); flex: none;
  }
  .contact-list svg { flex: none; }
</style>
</head>
<body>

  <section class="card card--front" aria-label="Card front">
    <div class="brand-mark">Rosalind<br>Thorpe<br>Gardens</div>
  </section>

  <section class="card card--back" aria-label="Card back">
    <div class="brand-mark">Rosalind<br>Thorpe<br>Gardens</div>

    <div class="contact-block">
      <h1 class="name">Corinne Haldwick</h1>
      <p class="role">Owner</p>
      <div class="divider"></div>
      <ul class="contact-list">
        <li>
          <svg width="10" height="10" viewBox="0 0 10 10" aria-hidden="true">
            <path d="M2.2 0.8 L3.8 2.8 L2.9 3.9 Q4 6.1 6.1 7.1 L7.2 6.2 L9.2 7.8 L8.2 9.3 Q1 8.6 0.7 1.8 Z" fill="#fff"/>
          </svg>
          913-555-0147
        </li>
        <li><span class="dot"></span>Rosalind Thorpe Gardens</li>
        <li><span class="dot"></span>@RosalindThorpeGardens</li>
        <li>
          <svg width="10" height="10" viewBox="0 0 10 10" aria-hidden="true">
            <circle cx="5" cy="5" r="4.3" fill="none" stroke="#fff" stroke-width="1"/>
            <ellipse cx="5" cy="5" rx="1.8" ry="4.3" fill="none" stroke="#fff" stroke-width="0.8"/>
            <line x1="0.7" y1="5" x2="9.3" y2="5" stroke="#fff" stroke-width="0.8"/>
          </svg>
          RosalindThorpeGardens.example
        </li>
      </ul>
    </div>
  </section>

</body>
</html>
```